Poster Design job - 11"x17" Poster for a Treasure Hunt

Summary:
This project is for a poster that will be used to promote a community treasure hunt for kids aged 9-14. This will be the 13th year we have run the treasure hunt. See the files for previous posters we have used (all from ArtForge).
***Please thoroughly read below before embarking on this project.
We loved everything about the 2012 design, particularly how all of the elements seem to belong exactly where they are on the poster. Previous years designs just had text blocks thrown on top of a background image which doesn't make a for a good poster; if within a few seconds you don’t have an idea about what even the poster is promoting, and if you can’t read every part of the poster from 6 feet away, the poster isn't working. Some of our other favorite posters for you to see are from 2012, 2016, and 2017 (attached).
Please make the Pine Hollow Quest Seekers logo a featured part of the design. See the 2012 poster winner where the logo was right at the top and very prominent.
Style: Scary, but remember the event is for children 9-14years old. The title of the hunt this year is "The Dreadful Saga of Bone Masts"
We want the Mexican Pirate to look scary with the following elements:
- the time period is the Late 1700s
- Use the pirate pic attached as a starting point to create the mexican pirate. That pic is only meant as a reference. Do not copy this pic direclty as there are probably copyrights on it.
- have a scary looking pirate ship in the background with a skull on its flag.
Poster must contain these texts:
event name: "The Dreadful Saga of Bone Masts"
"Be the First Team to unravel the mystery of the Venvaro Hoard and you will find a hidden Treasure chest and claim a FANTASTIC PRIZE!"
"Youth Ages 9-14 are able to participate.
"Team Applications are available on Sept 1st and due ASAP"
"Space is limited to the first 50 teams"
"Presented by Tom Fenwick of Hearth REaltors and Dr. Neil Ormsby of Pine Hollow Orthodontics"
"WWW.PHQUESTSEEKERS.EXAMPLE"
**Must include on the poster the logos of Tom Fenwick, Pine Hollow Orthodontics, and Pine Hollow Quest Seekers, event date of oct 13 2018.
_____
Remember, we want scary, but NOT gross and gruesome as this is for kids 9-14. Some of the poster submissions from previous years were way too gruesome with blood and gore. Do keep in mind this event is for children. For good examples, see the previous years posters attached.

```html
<!DOCTYPE html>
<html lang="en">
<head>
<meta charset="utf-8">
<title>The Dreadful Saga of Bone Masts – Pine Hollow Quest Seekers</title>
<link rel="stylesheet" href="https://fonts.googleapis.com/css2?family=Bangers&family=Oswald:wght@500&family=Rubik+Dirt&display=swap">
<style>
  :root {
    --night: #0d0f12;
    --storm: #3a4048;
    --mist: #6b727b;
    --bone: #f4f4f0;
    --blood-red: #e0141b;
    --gold: #f2e51d;
    --amber: #f0a21c;
    --coat-red: #8e1a1a;
    --coat-dark: #2a1512;
  }
  * { margin: 0; padding: 0; box-sizing: border-box; }
  html, body { width: 820px; height: 1200px; overflow: hidden; background: var(--night); }
  .poster {
    position: relative;
    width: 820px;
    height: 1200px;
    overflow: hidden;
    color: var(--bone);
    font-family: "Bangers", cursive;
    text-align: center;
  }
  .scene-backdrop {
    position: absolute; inset: 0;
    background:
      radial-gradient(ellipse 60% 40% at 25% 25%, var(--mist) 0%, transparent 70%),
      radial-gradient(ellipse 50% 30% at 30% 75%, var(--storm) 0%, transparent 75%),
      linear-gradient(180deg, #2b3037 0%, #1c2026 45%, #22272d 70%, var(--night) 100%);
  }
  .pirate-figure {
    position: absolute;
    left: 470px; top: 400px;
    width: 340px; height: 700px;
    border-radius: 140px 140px 20px 20px;
    background:
      radial-gradient(ellipse 30% 12% at 48% 8%, var(--coat-dark) 0%, transparent 100%),
      radial-gradient(ellipse 50% 40% at 50% 40%, var(--coat-red) 0%, transparent 80%),
      linear-gradient(180deg, rgba(42,21,18,0.9) 0%, rgba(110,24,22,0.85) 40%, rgba(30,20,20,0.8) 100%);
    opacity: 0.8;
  }
  .line { position: absolute; left: 0; right: 0; }
  .club-name {
    top: 66px;
    font-family: "Oswald", sans-serif; font-weight: 500;
    font-size: 40px; letter-spacing: 2px; text-transform: uppercase;
    color: var(--bone);
  }
  .era {
    top: 176px;
    font-family: "Bangers", cursive;
    font-size: 84px; letter-spacing: 2px;
    color: var(--blood-red); line-height: 1;
  }
  .title-lead {
    top: 262px;
    font-family: "Rubik Dirt", sans-serif; font-weight: 400;
    font-size: 52px; line-height: 1; text-transform: uppercase;
  }
  .title-main {
    top: 322px;
    font-family: "Rubik Dirt", sans-serif;
    font-size: 82px; line-height: 1; text-transform: uppercase;
  }
  .rule {
    position: absolute; left: 368px; width: 84px; height: 3px;
    background: var(--blood-red);
  }
  .rule-top { top: 436px; }
  .rule-bottom { top: 514px; }
  .event-date {
    top: 446px;
    font-size: 50px; color: var(--gold); line-height: 1.1;
  }
  .challenge {
    position: absolute; left: 40px; top: 562px;
    text-align: left; font-size: 27px; line-height: 34px;
  }
  .prize {
    position: absolute; top: 694px; left: 38px;
    font-family: "Bangers", cursive;
    font-size: 64px; letter-spacing: 1px;
    color: var(--blood-red); line-height: 1.1;
    text-align: left;
  }
  .eligibility { top: 850px; font-size: 35px; }
  .applications { top: 893px; font-size: 24px; color: var(--gold); }
  .team-limit { top: 948px; font-size: 38px; color: var(--gold); }
  .presented-label { top: 1016px; font-size: 24px; color: var(--amber); }
  .sponsors { top: 1046px; font-size: 24px; line-height: 30px; }
  .website { top: 1130px; font-size: 40px; color: var(--gold); }
  .sponsor-mark {
    position: absolute;
    font-family: "Oswald", sans-serif; font-weight: 500;
    color: var(--bone); text-transform: uppercase; line-height: 1.15;
  }
  .sponsor-realtor { left: 30px; top: 1128px; width: 130px; font-size: 18px; text-align: left; }
  .sponsor-ortho { right: 24px; top: 1124px; width: 140px; font-size: 16px; text-align: right; }
</style>
</head>
<body>
<main class="poster">
  <div class="scene-backdrop" role="img" aria-label="Stormy night sea with ghostly pirate ships flying skull flags"></div>
  <div class="pirate-figure" role="img" aria-label="Scary late-1700s pirate captain in a red coat and tricorn hat holding a pistol"></div>

  <p class="line club-name">Pine Hollow Quest Seekers</p>
  <p class="line era">1700s</p>
  <h1 class="line title-lead">The Dreadful Saga of</h1>
  <p class="line title-main">Bone Masts</p>

  <span class="rule rule-top"></span>
  <p class="line event-date">OCTOBER 13 2018</p>
  <span class="rule rule-bottom"></span>

  <p class="challenge">BE THE FIRST TEAM TO UNRAVEL THE<br>MYSTERY OF THE VENVARO HOARD<br>AND YOU WILL FIND A HIDDEN<br>TREASURE CHEST AN CLAIM A</p>
  <p class="prize">FANTASTIC PRIZE!</p>

  <p class="line eligibility">YOUTH AGES 9-14 ARE ABLE TO PARTICIPATE.</p>
  <p class="line applications">TEAM APPLICATIONS ARE AVAILABLE ON SEPT 1ST AND DUE ASAP</p>
  <p class="line team-limit">SPACE IS LIMITED TO THE FIRST 50 TEAMS</p>

  <p class="line presented-label">PRESENTED BY</p>
  <p class="line sponsors">TOM FENWICK OF HEARTH REALTORS AND DR. NEIL ORMSBY<br>OF PINE HOLLOW ORTHODONTICS</p>
  <p class="line website">WWW.PHQUESTSEEKERS.EXAMPLE</p>

  <p class="sponsor-mark sponsor-realtor">Tom Fenwick</p>
  <p class="sponsor-mark sponsor-ortho">Pine Hollow Orthodontics</p>
</main>
</body>
</html>
```